Private Investment Firm Needs PowerPoint Presentation Template

Design PowerPoint template, take Pinebrook-submitted rough presentation draft, and drop it into new template. See attached Project Brief file for more detail.
Updates

Some decent designs have been submitted but they seem to lack the understanding of our target markets. I am hopeful that more time and feedback will result in better results.

Target Market(s)

Private company owners and intermediaries.

Font styles to use
Serif

Colors
3176b5

Requirements
Must have
• See attached Project Brief.
Nice to have
Should not have
• No B2C fluff--this is a B2B project.

```html
<!DOCTYPE html>
<html lang="en">
<head>
<meta charset="utf-8">
<title>Contact – Pinebrook Capital</title>
<link href="https://fonts.googleapis.com/css2?family=Figtree:wght@400;600&family=Libre+Baskerville&display=swap" rel="stylesheet">
<style>
  :root{
    --brand-blue:#0a6fc2;
    --bar-blue:#0b6bbd;
    --ink:#3a3a3a;
    --paper:#ffffff;
    --photo-dark:#1e2636;
    --photo-mid:#3c4a66;
  }
  html,body{margin:0;padding:0;overflow:hidden;background:var(--paper);}
  .slide{position:relative;width:1200px;height:676px;overflow:hidden;background:var(--paper);font-family:"Figtree",sans-serif;color:var(--ink);}
  .side-bar{position:absolute;left:0;top:0;width:44px;height:100%;background:var(--bar-blue);}
  .edge-bar{position:absolute;right:0;top:0;width:11px;height:100%;background:var(--bar-blue);}
  .site-url{position:absolute;left:22px;top:336px;transform:translate(-50%,-50%) rotate(-90deg);white-space:nowrap;font-family:"Libre Baskerville",serif;font-size:14px;color:#fff;}
  .page-number{position:absolute;right:22px;top:18px;font-family:"Libre Baskerville",serif;font-size:17px;color:#222;}
  .slide-title{position:absolute;left:86px;top:80px;margin:0;font-size:30px;font-weight:600;color:var(--brand-blue);letter-spacing:.5px;}
  .office{position:absolute;left:86px;margin:0;}
  .office h2{margin:0 0 2px;font-size:24px;font-weight:600;color:var(--brand-blue);line-height:1.2;}
  .office p{margin:0;font-size:17.5px;line-height:24px;letter-spacing:.3px;}
  .office--east{top:178px;}
  .office--west{top:302px;}
  .person{position:absolute;right:491px;top:438px;text-align:right;}
  .person h2{margin:0 0 4px;font-size:25px;font-weight:600;color:var(--brand-blue);}
  .person p{margin:0;font-size:17px;line-height:22.4px;letter-spacing:.2px;}
  .person .email{text-decoration:underline;text-decoration-color:#aaa;text-underline-offset:3px;}
  .portrait{position:absolute;left:780px;top:176px;width:352px;height:500px;border-radius:120px 120px 0 0;background:linear-gradient(180deg,var(--photo-mid),var(--photo-dark) 55%);}
  .brand{position:absolute;left:66px;top:614px;display:flex;align-items:center;gap:8px;}
  .brand-dot{width:30px;height:30px;border-radius:50%;background:var(--brand-blue);}
  .brand-name{font-size:20px;font-weight:600;color:var(--brand-blue);letter-spacing:1.5px;}
  .copyright{position:absolute;left:322px;top:630px;font-size:12px;color:#444;letter-spacing:.2px;}
</style>
</head>
<body>
<div class="slide">
  <div class="side-bar"></div>
  <div class="edge-bar"></div>
  <div class="site-url">www.pinebrookcapital.com</div>
  <div class="page-number">18</div>

  <h1 class="slide-title">CONTACT</h1>

  <section class="office office--east">
    <h2>Boston Office</h2>
    <p>40 Harbor Ridge Road, Suite 210</p>
    <p>Millbrook, MA 01877</p>
    <p>(978) 555-0140</p>
  </section>

  <section class="office office--west">
    <h2>San Francisco Office</h2>
    <p>Two Alder Street, Suite 480</p>
    <p>Oakview, CA 94622</p>
    <p>(415) 555-0188</p>
  </section>

  <section class="person">
    <h2>Daniel R. Marchetti</h2>
    <p>Principal</p>
    <p>17 Cedar Hollow Road, Suite 300</p>
    <p>Fairhaven, CT&nbsp; 06899</p>
    <p>Direct: (978) 555-0152</p>
    <p class="email">dmarchetti@pinebrookcapital.com</p>
  </section>

  <div class="portrait" role="img" aria-label="Portrait photo of the principal in a dark blazer and blue shirt, arms crossed"></div>

  <div class="brand">
    <span class="brand-dot"></span>
    <span class="brand-name">PINEBROOK</span>
  </div>
  <div class="copyright">Copyright © 2018 ◆ Pinebrook Capital Partners ◆ All Rights Reserved</div>
</div>
</body>
</html>
```